Tallowood building company Business card design

I need a business card design for my company. I have a logo but dont have business cards with our logo..

www.tallowoodbuildingco.com.au

The logo is on the website

I need the same details as this design I have attached. we have changed the logo and colours. just like the website

Building

```html
<!DOCTYPE html>
<html lang="en">
<head>
<meta charset="utf-8">
<title>Tallowood Building – Business Card</title>
<link rel="stylesheet" href="https://fonts.googleapis.com/css2?family=Fira+Sans+Condensed:wght@500;600&family=Fira+Sans:wght@300;400;600&display=swap">
<style>
  :root {
    --backdrop: #2a2a2c;
    --card-white: #ffffff;
    --brand-blue: #1a82bf;
    --text-grey: #5f6468;
    --line-light: #a9d2ec;
    --text-white: #ffffff;
    --text-soft: #d5e9f6;
  }
  * { margin: 0; padding: 0; box-sizing: border-box; }
  html, body {
    width: 1200px; height: 799px; overflow: hidden;
    background: var(--backdrop);
  }
  .card {
    position: absolute; left: 160px; top: 130px;
    width: 880px; height: 538px;
    display: flex;
    box-shadow: 0 10px 30px rgba(0,0,0,.45);
    font-family: "Fira Sans", sans-serif;
  }
  .card__brand-side {
    width: 340px; background: var(--card-white);
    display: flex; flex-direction: column; align-items: center;
    padding: 34px 26px 30px;
  }
  .services {
    list-style: none; text-align: center;
    color: var(--text-grey); font-weight: 300; font-size: 17px; line-height: 1.35;
  }
  .services li { display: inline; }
  .services li::before { content: "• "; color: var(--brand-blue); }
  .services li + li { margin-left: 8px; }
  .brand-mark {
    margin-top: 46px;
    display: flex; flex-direction: column; align-items: center; gap: 22px;
  }
  .brand-mark__square {
    width: 64px; height: 64px; background: var(--brand-blue);
  }
  .brand-mark__name {
    color: var(--brand-blue); font-weight: 600;
    font-size: 38px; line-height: 1.1; text-align: center;
    letter-spacing: 1px; text-transform: uppercase;
  }
  .website {
    margin-top: auto;
    font-size: 18px; color: var(--text-grey); font-weight: 400;
  }
  .website strong { color: var(--brand-blue); font-weight: 600; }
  .card__contact-side {
    flex: 1; background: var(--brand-blue); position: relative;
    color: var(--text-white);
  }
  .person { position: absolute; top: 180px; left: 0; right: 0; text-align: center; }
  .person__name {
    font-family: "Fira Sans Condensed", sans-serif; font-weight: 600;
    font-size: 34px; letter-spacing: .5px;
  }
  .person__role { font-weight: 300; font-size: 19px; color: var(--text-soft); margin-top: 2px; }
  .divider {
    position: absolute; top: 262px; left: 120px; right: 40px;
    height: 1px; background: var(--line-light);
  }
  .divider::before {
    content: ""; position: absolute; left: -3px; top: -3px;
    width: 7px; height: 7px; border-radius: 50%; background: var(--text-white);
  }
  .contacts {
    position: absolute; top: 330px; left: 0; right: 0;
    list-style: none; text-align: center;
    font-size: 21px; font-weight: 400; line-height: 1.55;
  }
  .contacts b { font-weight: 600; }
</style>
</head>
<body>
  <article class="card">
    <section class="card__brand-side">
      <ul class="services">
        <li>New Homes</li><li>Additions &amp; Renovations</li><li>Domestic &amp; Commercial Builders</li>
      </ul>
      <div class="brand-mark">
        <span class="brand-mark__square"></span>
        <p class="brand-mark__name">Tallowood<br>Building</p>
      </div>
      <p class="website"><strong>www.</strong>tallowoodbuildingco.com.au</p>
    </section>
    <section class="card__contact-side">
      <div class="person">
        <h1 class="person__name">Marek Dalton</h1>
        <p class="person__role">Director</p>
      </div>
      <div class="divider"></div>
      <ul class="contacts">
        <li><b>p:</b> 08 9000 4180</li>
        <li><b>m:</b> 0400 552 916</li>
        <li><b>e:</b> info@tallowoodbuildingco.com.au</li>
      </ul>
    </section>
  </article>
</body>
</html>
```